Brisk Coatings business card for residential and commercial painting

A clean, professional design. Easy to read
Eye catching and elegant
Front could have some color variations
On the back of card I would like all black with signature logo

*Attached is my current business card and the items I want displayed

Contact Information for Business Card

Email, phone number, website, and owner name

Font styles to use
Serif

Requirements
Must have
• My logo with cool design and perhaps some paint splatter

```html
<!DOCTYPE html>
<html lang="en">
<head>
<meta charset="utf-8">
<title>Brisk Coatings – Business Card</title>
<link rel="stylesheet" href="https://fonts.googleapis.com/css2?family=Oswald:wght@500&family=Roboto:wght@400;500&display=swap">
<style>
  :root {
    --backdrop: #6b6768;
    --card-dark: #333336;
    --card-light: #f4f4f4;
    --note-line: #b9b9b9;
    --ink-deep: #151516;
    --ink-white: #ffffff;
    --accent-blue: #1a6fc0;
  }
  * { margin: 0; padding: 0; box-sizing: border-box; }
  html, body {
    width: 1200px;
    height: 1200px;
    overflow: hidden;
    background: var(--backdrop);
  }
  .canvas {
    position: relative;
    width: 1200px;
    height: 1200px;
  }
  .card {
    position: absolute;
    width: 594px;
    height: 350px;
    border-radius: 20px;
    overflow: hidden;
    background: var(--card-dark);
  }

  /* Back card */
  .card--back { left: 298px; top: 198px; }
  .card--back .back-band {
    position: absolute;
    left: 0; right: 0; top: 0;
    height: 210px;
    background: var(--card-dark);
  }
  .card--back .note-area {
    position: absolute;
    left: 0; right: 0; bottom: 0;
    height: 140px;
    background: var(--card-light);
  }
  .note-line {
    position: absolute;
    left: 35px; right: 34px;
    height: 2px;
    background: var(--note-line);
  }
  .note-line:nth-child(1) { top: 36px; }
  .note-line:nth-child(2) { top: 71px; }
  .note-line:nth-child(3) { top: 106px; }
  .back-wordmark {
    position: absolute;
    left: 0; right: 0; top: 76px;
    text-align: center;
    font-family: "Oswald", sans-serif;
    font-weight: 500;
    font-size: 54px;
    line-height: 1;
    letter-spacing: 0.5px;
    color: var(--ink-deep);
    text-transform: uppercase;
  }

  /* Front card */
  .card--front { left: 292px; top: 636px; }
  .front-wordmark {
    position: absolute;
    left: 37px; top: 62px;
    font-family: "Oswald", sans-serif;
    font-weight: 500;
    font-size: 41px;
    line-height: 1;
    color: var(--ink-white);
    text-transform: uppercase;
  }
  .brand-art {
    position: absolute;
    left: 464px; top: 0;
    width: 92px;
    height: 350px;
    border-radius: 10px 10px 0 0;
    background: linear-gradient(180deg, var(--accent-blue) 0%, var(--accent-blue) 62%, var(--ink-white) 72%, var(--ink-white) 100%);
  }
  .owner-name {
    position: absolute;
    left: 36px; top: 187px;
    font-family: "Roboto", sans-serif;
    font-weight: 500;
    font-size: 22px;
    color: var(--accent-blue);
  }
  .owner-role {
    position: absolute;
    left: 36px; top: 214px;
    font-family: "Roboto", sans-serif;
    font-weight: 400;
    font-size: 15.5px;
    color: var(--ink-white);
  }
  .contact-list {
    position: absolute;
    left: 36px; top: 245px;
    list-style: none;
  }
  .contact-item {
    display: flex;
    align-items: center;
    height: 21px;
    font-family: "Roboto", sans-serif;
    font-size: 15.5px;
    color: var(--ink-white);
  }
  .contact-item svg {
    width: 15px;
    height: 15px;
    margin-right: 12px;
    fill: var(--accent-blue);
  }
</style>
</head>
<body>
<main class="canvas">

  <section class="card card--back" aria-label="Card back">
    <div class="back-band"></div>
    <div class="back-wordmark">Brisk Coatings</div>
    <div class="note-area">
      <span class="note-line"></span>
      <span class="note-line"></span>
      <span class="note-line"></span>
    </div>
  </section>

  <section class="card card--front" aria-label="Card front">
    <div class="front-wordmark">Brisk Coatings</div>
    <div class="brand-art" role="img" aria-label="Large blue and white brand artwork area"></div>
    <p class="owner-name">Marcus "MC"</p>
    <p class="owner-role">Owner - Licensed &amp; Insured</p>
    <ul class="contact-list">
      <li class="contact-item">
        <svg viewBox="0 0 16 16" aria-hidden="true"><path d="M3 2h3l1.2 3-1.7 1.2a8 8 0 0 0 4.3 4.3L11 8.8l3 1.2v3a1 1 0 0 1-1 1A11 11 0 0 1 2 3a1 1 0 0 1 1-1z"/></svg>
        931-555-0147
      </li>
      <li class="contact-item">
        <svg viewBox="0 0 16 16" aria-hidden="true"><path d="M1 3h14v10H1z"/><path d="M2.5 4.5 8 9l5.5-4.5" fill="none" stroke="var(--card-dark)" stroke-width="1.2"/></svg>
        briskcoatingstn@mailbox.com
      </li>
      <li class="contact-item">
        <svg viewBox="0 0 16 16" aria-hidden="true"><circle cx="8" cy="8" r="7"/><path d="M1 8h14M8 1c-3 3.5-3 10.5 0 14M8 1c3 3.5 3 10.5 0 14" fill="none" stroke="var(--card-dark)" stroke-width="1"/></svg>
        www.briskcoatingstn.com
      </li>
    </ul>
  </section>

</main>
</body>
</html>
```